Business Card Design

WE are looking for a premium quality Business Cards for a Law Firm . Copies of our current business card is attached.

Contact Information for Business Card

xyz

```html
<!DOCTYPE html>
<html lang="en">
<head>
<meta charset="utf-8">
<title>Ashbury Lawyers – Business Card</title>
<link href="https://fonts.googleapis.com/css2?family=Cinzel:wght@600&family=Arimo:wght@400;700&display=swap" rel="stylesheet">
<style>
  :root {
    --backdrop: #141414;
    --card: #262626;
    --card-deep: #1e1e1e;
    --gold: #c9953f;
    --white: #f4f4f2;
    --muted: #e2e2e2;
  }
  * { box-sizing: border-box; margin: 0; padding: 0; }
  html, body { width: 1200px; height: 963px; overflow: hidden; }
  body {
    background: var(--backdrop);
    display: flex;
    align-items: center;
    justify-content: center;
    gap: 40px;
    font-family: "Arimo", Arial, sans-serif;
  }
  .card {
    position: relative;
    width: 530px;
    height: 303px;
    border-radius: 22px;
    background: var(--card);
    border: 2px solid var(--gold);
    overflow: hidden;
  }
  /* Brand lockup */
  .brand {
    position: absolute;
    display: flex;
    flex-direction: column;
    align-items: center;
  }
  .brand-circle {
    width: 66px;
    height: 66px;
    border-radius: 50%;
    border: 4px solid var(--gold);
    margin-bottom: 12px;
  }
  .brand-name {
    font-family: "Cinzel", Georgia, serif;
    font-weight: 600;
    color: var(--white);
    text-align: center;
    line-height: 1.1;
  }
  .brand-name .primary { display: block; font-size: 36px; letter-spacing: 1px; }
  .brand-name .secondary { display: block; font-size: 12px; letter-spacing: 9px; margin-top: 4px; }
  .brand-rule {
    display: flex; align-items: center; gap: 8px; width: 100%;
  }
  .brand-rule::before, .brand-rule::after {
    content: ""; flex: 1; height: 1px; background: var(--gold);
  }
  /* Front */
  .front .brand { left: 28px; top: 62px; width: 225px; }
  .divider { position: absolute; left: 250px; top: 30px; }
  .details {
    position: absolute;
    left: 285px;
    top: 44px;
    color: var(--muted);
    font-size: 11.5px;
    line-height: 1.45;
  }
  .person-name {
    color: var(--gold);
    font-weight: 700;
    font-size: 21px;
    letter-spacing: 0.5px;
    text-transform: uppercase;
    line-height: 1.1;
  }
  .person-role { text-transform: uppercase; font-size: 10.5px; letter-spacing: 0.3px; }
  .address { margin-top: 8px; }
  .contacts { list-style: none; margin-top: 10px; }
  .contacts li { display: flex; align-items: center; gap: 8px; }
  .contacts svg { width: 12px; height: 12px; flex: none; }
  /* Back */
  .pattern-field {
    position: absolute; inset: 0;
    background: radial-gradient(circle at 70% 60%, #2e2e2e 0%, var(--card) 45%, var(--card-deep) 100%);
  }
  .back .brand {
    left: 0; right: 0; top: 50%;
    transform: translateY(-50%);
    flex-direction: row;
    justify-content: center;
    gap: 16px;
  }
  .back .brand-circle { margin-bottom: 0; }
</style>
</head>
<body>
  <section class="card front" aria-label="Business card front">
    <div class="brand">
      <div class="brand-circle"></div>
      <div class="brand-name">
        <span class="primary">ASHBURY</span>
        <span class="brand-rule"><span class="secondary">LAWYERS</span></span>
      </div>
    </div>

    <svg class="divider" width="40" height="240" viewBox="0 0 40 240" aria-hidden="true">
      <line x1="38" y1="0" x2="2" y2="240" stroke="#d8d8d8" stroke-width="1.2"/>
    </svg>

    <div class="details">
      <p class="person-name">Daniel Reeve</p>
      <p class="person-role">Director &amp; Principal Solicitor</p>
      <p>MBA, Juris Doctor</p>
      <p class="address">Level 3, Carrow House<br>48 Carrow Terrace,<br>Milton, QLD 4064</p>
      <ul class="contacts">
        <li>
          <svg viewBox="0 0 24 24" fill="none" stroke="#c9953f" stroke-width="2"><path d="M5 3h4l2 5-3 2a12 12 0 0 0 6 6l2-3 5 2v4a2 2 0 0 1-2 2A17 17 0 0 1 3 5a2 2 0 0 1 2-2z"/></svg>
          +61730001234
        </li>
        <li>
          <svg viewBox="0 0 24 24" fill="none" stroke="#c9953f" stroke-width="2"><rect x="6" y="2" width="12" height="20" rx="2"/><line x1="11" y1="18" x2="13" y2="18"/></svg>
          +61 0400 123 456
        </li>
        <li>
          <svg viewBox="0 0 24 24" fill="none" stroke="#c9953f" stroke-width="2"><rect x="2" y="5" width="20" height="14" rx="1"/><path d="M2 6l10 7 10-7"/></svg>
          daniel@ashburylawyers.com.au
        </li>
        <li>
          <svg viewBox="0 0 24 24" fill="none" stroke="#c9953f" stroke-width="2"><circle cx="12" cy="12" r="10"/><path d="M2 12h20M12 2c3 3 3 17 0 20M12 2c-3 3-3 17 0 20"/></svg>
          www.ashburylawyers.com.au
        </li>
      </ul>
    </div>
  </section>

  <section class="card back" aria-label="Business card back">
    <div class="pattern-field" role="img" aria-label="Embossed repeating brand pattern in dark tones"></div>
    <div class="brand">
      <div class="brand-circle"></div>
      <div class="brand-name">
        <span class="primary">ASHBURY</span>
        <span class="brand-rule"><span class="secondary">LAWYERS</span></span>
      </div>
    </div>
  </section>
</body>
</html>
```